Talvique Hotels Business Card and Logo

We need a business card design for a hotel group. I saw a hotel card you designed and really liked it. We have multiple properties with different brands. Were hoping that the card would be unique and find a way to list out all our properties. Our web address is www.talviquehotels.com. I have attached some photos of card designs I like.

Industry/Entity Type

Hotel

Contact Information for Business Card

Scott CurranReneson HotelsChief Operating Officer56 Madera DriveCorte Madera, CA 94925Office 415-891-5013Cell 707-5550143

```html
<!DOCTYPE html>
<html lang="en">
<head>
<meta charset="utf-8">
<title>Talvique Hotels Business Card</title>
<link rel="stylesheet" href="https://fonts.googleapis.com/css2?family=Cormorant+Garamond:wght@400;500;600;700&display=swap">
<style>
  :root {
    --backdrop: #2b2b2d;
    --card-teal: #0c2d37;
    --card-teal-edge: #113a45;
    --card-gold: #c3b655;
    --gold-ink: #c9b552;
    --teal-ink: #163a44;
    --rule: #1f4a55;
  }
  * { margin: 0; padding: 0; box-sizing: border-box; }
  html, body { width: 1200px; height: 900px; overflow: hidden; }
  body {
    background: var(--backdrop);
    font-family: "Cormorant Garamond", Georgia, serif;
    display: flex;
    align-items: center;
    justify-content: center;
    gap: 90px;
  }
  .card {
    width: 340px;
    height: 620px;
    position: relative;
    display: flex;
    flex-direction: column;
    align-items: center;
  }
  .card--front {
    background: var(--card-teal);
    border-left: 10px solid var(--card-teal-edge);
    color: var(--gold-ink);
  }
  .card--back {
    background: var(--card-gold);
    color: var(--teal-ink);
  }
  .brand {
    position: absolute;
    top: 270px;
    left: 0; right: 0;
    display: flex;
    flex-direction: column;
    align-items: center;
    gap: 14px;
  }
  .brand__dot {
    width: 14px; height: 14px;
    border-radius: 50%;
    background: var(--gold-ink);
  }
  .brand__name {
    font-size: 30px;
    font-weight: 500;
    letter-spacing: 0.5px;
    text-align: center;
    line-height: 1.1;
  }
  .website {
    position: absolute;
    bottom: 70px;
    left: 0; right: 0;
    text-align: center;
    font-size: 17px;
    letter-spacing: 0.3px;
  }
  .contact {
    margin-top: 170px;
    text-align: center;
    width: 100%;
  }
  .contact__name {
    font-size: 19px;
    font-weight: 700;
  }
  .contact__title {
    font-size: 14px;
    margin-top: 2px;
  }
  .phones {
    margin-top: 22px;
    list-style: none;
    display: inline-flex;
    flex-direction: column;
    gap: 3px;
    font-size: 14px;
  }
  .phones li { display: flex; align-items: center; gap: 5px; }
  .phones svg { width: 11px; height: 11px; fill: var(--teal-ink); }
  .divider {
    width: 220px;
    height: 1.5px;
    background: var(--rule);
    margin: 18px auto 20px;
  }
  .address {
    font-style: normal;
    font-size: 14px;
    line-height: 1.3;
  }
</style>
</head>
<body>
  <section class="card card--front" aria-label="Card front">
    <div class="brand">
      <span class="brand__dot"></span>
      <span class="brand__name">Talvique Hotels</span>
    </div>
    <p class="website">www.talviquehotels.com</p>
  </section>

  <section class="card card--back" aria-label="Card back">
    <div class="contact">
      <h1 class="contact__name">Brent Holloway</h1>
      <p class="contact__title">Chief Operating Officer</p>
      <ul class="phones">
        <li>
          <svg viewBox="0 0 24 24" aria-hidden="true"><path d="M6.6 10.8a15 15 0 0 0 6.6 6.6l2.2-2.2a1 1 0 0 1 1-.25 11.4 11.4 0 0 0 3.6.57 1 1 0 0 1 1 1V20a1 1 0 0 1-1 1A17 17 0 0 1 3 4a1 1 0 0 1 1-1h3.5a1 1 0 0 1 1 1c0 1.25.2 2.45.57 3.57a1 1 0 0 1-.25 1z"/></svg>
          415-555-0186
        </li>
        <li>
          <svg viewBox="0 0 24 24" aria-hidden="true"><path d="M7 1h10a2 2 0 0 1 2 2v18a2 2 0 0 1-2 2H7a2 2 0 0 1-2-2V3a2 2 0 0 1 2-2zm0 3v14h10V4zm5 15.5a1 1 0 1 0 0 2 1 1 0 0 0 0-2z"/></svg>
          707-5550143
        </li>
      </ul>
      <div class="divider"></div>
      <address class="address">
        Talvique Hotels<br>
        83 Pellwick Lane<br>
        Larkvale, CA 94961
      </address>
    </div>
  </section>
</body>
</html>
```